Wordpress Design for a Private Label BBQ Brand

For our new brand, we'd need a new Wordpress website. We'd prefer to run the website on Wordpress

We'd like to include the following
- space for description of the brand
- space for product portfolio (not a shop!)
- space for socials
- space for support
- space for contact

```html
<!DOCTYPE html>
<html lang="en">
<head>
<meta charset="utf-8">
<title>Fornella — Grill Like a Pro</title>
<link href="https://fonts.googleapis.com/css2?family=Libre+Baskerville:wght@400;700&family=Poppins:wght@400;500;600&display=swap" rel="stylesheet">
<style>
:root{
  --ink:#0f0f10;
  --charcoal:#1b1b1c;
  --charcoal-2:#262627;
  --peach:#f8e1d6;
  --ember:#e8541c;
  --ember-deep:#c01a2a;
  --flame:#ef6a24;
  --blue:#3e7fc6;
  --blue-deep:#2c5aa6;
  --white:#ffffff;
  --muted:#9a9a9a;
  --grey-line:#6c6c6c;
  --text-dark:#222;
}
*{box-sizing:border-box;margin:0;padding:0}
html,body{width:1200px;height:3902px;overflow:hidden;background:var(--ink)}
body{font-family:'Poppins',sans-serif;color:var(--white)}
.page{position:relative;width:1200px;height:3902px;overflow:hidden;background:var(--ink)}
.abs{position:absolute}
.serif{font-family:'Libre Baskerville',serif;font-weight:700}
.dark-tex{background:radial-gradient(ellipse at 30% 40%,#2e2e2f 0%,#1c1c1d 55%,#121213 100%)}
.mark-dot{position:absolute;width:34px;height:34px;border-radius:50%;background:linear-gradient(160deg,var(--flame),var(--ember-deep))}
.mark-dot.sm{width:24px;height:24px}

/* header */
.site-header{left:0;top:0;width:1200px;height:144px;background:linear-gradient(180deg,#1a1a1b,#222223);border-bottom:1px solid #333}
.brand{left:100px;top:96px;font-size:21px;letter-spacing:1px}
.social{display:flex;gap:17px}
.social span{width:30px;height:30px;border-radius:50%;border:1.5px solid #8a8a8a;display:block}
.nav a{position:absolute;top:104px;font-family:'Libre Baskerville',serif;font-weight:700;font-size:13px;letter-spacing:1.5px;color:var(--white);text-decoration:none}
.nav-underline{left:368px;top:138px;width:62px;height:4px;background:linear-gradient(90deg,var(--flame),var(--ember-deep))}
.btn{display:flex;align-items:center;justify-content:center;font-family:'Libre Baskerville',serif;font-weight:700;font-size:12.5px;letter-spacing:1px;color:var(--white)}
.btn-ember{background:linear-gradient(90deg,var(--flame),var(--ember-deep))}
.btn-blue{background:linear-gradient(90deg,var(--blue),var(--blue-deep))}

/* hero */
.hero-photo{left:0;top:144px;width:1200px;height:680px;background:radial-gradient(ellipse at 25% 45%,#a46e47 0%,#6d5a35 35%,#4f5a2a 65%,#3a4620 100%)}
.hero-shade{left:0;top:144px;width:1200px;height:680px;background:rgba(20,14,8,.35)}
.hero-kicker{left:0;width:1270px;top:338px;text-align:center;color:var(--flame);font-size:15px;font-weight:600;letter-spacing:2px}
.hero-title{left:0;width:1270px;top:370px;text-align:center;font-size:62px;letter-spacing:1px}
.hero-sub{left:0;width:1200px;top:458px;text-align:center;font-size:13px;font-weight:600}

/* about */
.about-title{left:100px;top:938px;font-size:32px}
.copy{font-size:12px;line-height:20px;color:#e6e6e6}
.link-under{font-family:'Libre Baskerville',serif;font-weight:700;font-size:12.5px;text-decoration:underline;color:var(--white)}
.product-shot{border-radius:50%;background:radial-gradient(circle,#3a3a3b 0%,#1f1f20 70%)}

/* products */
.section-title{left:0;width:1200px;text-align:center;font-size:31px;color:var(--text-dark)}
.title-rule{left:523px;top:1401px;width:154px;height:4px;background:linear-gradient(90deg,var(--flame),var(--ember-deep))}
.product-card{background:var(--white);border-radius:6px;box-shadow:0 4px 14px rgba(0,0,0,.08)}
.product-card .pic{position:absolute;left:40px;right:40px;top:17px;height:256px;border-radius:4px;background:linear-gradient(180deg,#e9e9ea,#cfcfd1)}
.product-card h3{position:absolute;left:0;right:0;top:300px;text-align:center;font-weight:600;font-size:19px;color:var(--ember)}
.product-card p{position:absolute;left:0;right:0;top:337px;text-align:center;font-size:12px;color:var(--text-dark)}
.round-arrow{width:50px;height:50px;border-radius:50%;background:var(--white);box-shadow:0 2px 8px rgba(0,0,0,.15)}

/* blog */
.blog-card{background:var(--white);border-radius:5px;overflow:hidden}
.blog-card .pic{height:177px;background:radial-gradient(ellipse at 50% 70%,#c4551c 0%,#5a2a14 45%,#1d1b1a 100%)}
.blog-card .date{position:absolute;left:14px;top:12px;padding:3px 8px;border-radius:4px;background:var(--blue);font-size:12px;font-weight:600}
.blog-card h3{position:absolute;left:17px;top:196px;font-size:21px;font-weight:500;color:var(--text-dark)}
.blog-card p{position:absolute;left:15px;right:12px;top:230px;font-size:11.5px;line-height:19px;color:var(--muted)}
.ghost-arrow{width:36px;height:36px;border-radius:50%;border:1.5px solid #cfcfcf}

/* contact */
.field{border:1.5px solid #8a8a8a;font-size:12px;color:#9c9c9c;padding:20px 0 0 20px}

/* footer */
.foot-links a,.foot-legal a{position:absolute;font-size:12px;color:#d8d8d8;text-decoration:none}
</style>
</head>
<body>
<div class="page">

  <!-- header -->
  <header class="abs site-header dark-tex">
    <div class="mark-dot" style="left:140px;top:34px"></div>
    <div class="abs brand serif">FORNELLA</div>
    <div class="abs social" style="left:927px;top:24px"><span></span><span></span><span></span><span></span></div>
    <nav class="nav">
      <a style="left:376px">HOME</a>
      <a style="left:476px">ABOUT US</a>
      <a style="left:608px">PRODUCTS</a>
      <a style="left:746px">NEWS</a>
      <a style="left:843px">CONTACT</a>
    </nav>
    <div class="abs nav-underline"></div>
    <div class="abs btn btn-ember" style="left:977px;top:91px;width:121px;height:41px">BUY NOW</div>
  </header>

  <!-- hero -->
  <div class="abs hero-photo" role="img" aria-label="Smiling man grilling food outdoors while a family eats at a garden picnic table"></div>
  <div class="abs hero-shade"></div>
  <div class="abs hero-kicker">WELCOME TO FORNELLA</div>
  <h1 class="abs hero-title serif">GRILL LIKE A PRO</h1>
  <div class="abs hero-sub">PORTABLE BBQ GRILLS, ADDONS AND GRILLING ACCESSORIES</div>
  <div class="abs btn btn-blue" style="left:565px;top:508px;width:155px;height:39px">CONTACT NOW</div>

  <!-- section bands -->
  <svg class="abs" style="left:0;top:0" width="1200" height="3902" viewBox="0 0 1200 3902">
    <defs>
      <linearGradient id="emberGrad" x1="0" x2="1"><stop offset="0" stop-color="#ef6a24"/><stop offset="1" stop-color="#c01a2a"/></linearGradient>
      <linearGradient id="blueGrad" x1="0" x2="1"><stop offset="0" stop-color="#3e7fc6"/><stop offset="1" stop-color="#2c5aa6" stop-opacity=".4"/></linearGradient>
      <radialGradient id="char" cx=".3" cy=".4" r=".9"><stop offset="0" stop-color="#2e2e2f"/><stop offset=".6" stop-color="#1c1c1d"/><stop offset="1" stop-color="#121213"/></radialGradient>
    </defs>
    <!-- about -->
    <polygon points="0,803 1200,740 1200,1250 0,1290" fill="url(#char)"/>
    <polygon points="620,770 1200,720 1200,775" fill="url(#emberGrad)"/>
    <!-- products -->
    <polygon points="0,1332 1200,1248 1200,1900 0,1985" fill="#f8e1d6"/>
    <polygon points="0,1250 560,1292 0,1332" fill="url(#blueGrad)"/>
    <!-- accessories -->
    <polygon points="0,1985 1200,1896 1200,2460 0,2460" fill="url(#char)"/>
    <polygon points="650,1940 1200,1896 1200,1977" fill="url(#emberGrad)"/>
    <!-- blog -->
    <polygon points="0,2455 1200,2400 1200,3030 0,3030" fill="#000"/>
    <polygon points="0,2365 650,2412 0,2455" fill="url(#blueGrad)"/>
    <!-- contact -->
    <rect x="0" y="3030" width="1200" height="530" fill="url(#char)"/>
    <!-- footer -->
    <polygon points="0,3520 1200,3470 1200,3902 0,3902" fill="#0b0b0b"/>
    <polygon points="610,3528 1200,3470 1200,3560" fill="url(#emberGrad)"/>
    <line x1="150" y1="3807" x2="1050" y2="3807" stroke="#2a2a2a" stroke-width="1"/>
    <!-- arrows -->
    <polyline points="113,1639 105,1647 113,1655" fill="none" stroke="#333" stroke-width="2"/>
    <polyline points="1099,1639 1107,1647 1099,1655" fill="none" stroke="#333" stroke-width="2"/>
    <line x1="50" y1="2756" x2="64" y2="2756" stroke="#cfcfcf" stroke-width="1.5"/>
    <polyline points="54,2752 50,2756 54,2760" fill="none" stroke="#cfcfcf" stroke-width="1.5"/>
    <line x1="1146" y1="2756" x2="1160" y2="2756" stroke="#cfcfcf" stroke-width="1.5"/>
    <polyline points="1156,2752 1160,2756 1156,2760" fill="none" stroke="#cfcfcf" stroke-width="1.5"/>
  </svg>

  <!-- about -->
  <div class="mark-dot" style="left:104px;top:878px"></div>
  <h2 class="abs about-title serif">ABOUT FORNELLA</h2>
  <p class="abs copy" style="left:100px;top:990px;width:500px">Lorem Ipsum is simply dummy text of the printing and typesetting industry. Lorem Ipsum has been the industry's standard dummy text ever since the 1500s, when an unknown printer took a galley of type and scrambled it to make a type specimen book. It has survived not only five centuries, but also the leap into electronic typesetting</p>
  <div class="abs link-under" style="left:100px;top:1129px">MORE ABOUT US</div>
  <div class="abs product-shot" style="left:682px;top:795px;width:330px;height:330px" role="img" aria-label="Black ceramic kamado grill on a three-legged stand"></div>

  <!-- products -->
  <h2 class="abs section-title serif" style="top:1352px">PRODUCTS</h2>
  <div class="abs title-rule"></div>
  <div class="abs product-card" style="left:98px;top:1453px;width:308px;height:388px">
    <div class="pic" role="img" aria-label="Kamado grill product photo"></div>
    <h3>Product Name</h3><p>Desription goes here</p>
  </div>
  <div class="abs product-card" style="left:445px;top:1453px;width:308px;height:388px">
    <div class="pic" role="img" aria-label="Grill tool set in an aluminium case"></div>
    <h3>Product Name</h3><p>Desription goes here</p>
  </div>
  <div class="abs product-card" style="left:791px;top:1453px;width:308px;height:388px">
    <div class="pic" role="img" aria-label="Grilling tongs, fork and spatula"></div>
    <h3>Product Name</h3><p>Desription goes here</p>
  </div>
  <div class="abs round-arrow" style="left:84px;top:1622px;z-index:-0"></div>
  <div class="abs round-arrow" style="left:1078px;top:1622px"></div>
  <svg class="abs" style="left:0;top:1600px" width="1200" height="100" viewBox="0 1600 1200 100">
    <polyline points="113,1639 105,1647 113,1655" fill="none" stroke="#333" stroke-width="2"/>
    <polyline points="1099,1639 1107,1647 1099,1655" fill="none" stroke="#333" stroke-width="2"/>
  </svg>

  <!-- accessories -->
  <div class="abs" style="left:0;top:2060px;width:409px;height:273px;background:linear-gradient(150deg,#9aa3ad,#5e6670 60%,#2a2d31);clip-path:polygon(40% 0,100% 40%,60% 100%,0 100%,0 70%)" role="img" aria-label="Stainless steel grill spatula"></div>
  <div class="mark-dot sm" style="left:476px;top:2059px"></div>
  <h2 class="abs serif" style="left:515px;top:2054px;font-size:31px">ACCESSORIES</h2>
  <p class="abs copy" style="left:480px;top:2118px;width:500px">Lorem Ipsum is simply dummy text of the printing and typesetting industry. Lorem Ipsum has been the industry's standard dummy text ever since the 1500s, when an unknown printer took a galley of type and scrambled it to make a type specimen book. It has survived not only five centuries, but also the leap into electronic typesetting</p>
  <div class="abs btn btn-blue" style="left:483px;top:2242px;width:226px;height:41px">VIEW OUR ACCESSORIES</div>

  <!-- blog -->
  <div class="mark-dot sm" style="left:452px;top:2520px"></div>
  <h2 class="abs serif" style="left:492px;top:2516px;font-size:30px">LATEST BLOG</h2>
  <article class="abs blog-card" style="left:117px;top:2588px;width:307px;height:336px">
    <div class="pic" role="img" aria-label="Corn and skewers on a charcoal grill"></div>
    <span class="date">July 30,2019</span>
    <h3>Lorem Ipsum is a dummy</h3>
    <p>Lorem Ipsum is simply dummy text of the a printing and typesetting ever since indus-try Lorem Ipsum is simply dummy text of</p>
  </article>
  <article class="abs blog-card" style="left:450px;top:2588px;width:308px;height:336px">
    <div class="pic" role="img" aria-label="Meat searing over open flames"></div>
    <span class="date">July 25,2019</span>
    <h3>Lorem Ipsum is a dummy</h3>
    <p>Lorem Ipsum is simply dummy text of the a printing and typesetting ever since indus-try Lorem Ipsum is simply dummy text of</p>
  </article>
  <article class="abs blog-card" style="left:783px;top:2588px;width:308px;height:336px">
    <div class="pic" role="img" aria-label="Tongs turning food on a flaming grill at dusk"></div>
    <span class="date">July 22,2019</span>
    <h3>Lorem Ipsum is a dummy</h3>
    <p>Lorem Ipsum is simply dummy text of the a printing and typesetting ever since indus-try Lorem Ipsum is simply dummy text of</p>
  </article>
  <div class="abs ghost-arrow" style="left:39px;top:2738px"></div>
  <div class="abs ghost-arrow" style="left:1135px;top:2738px"></div>
  <svg class="abs" style="left:0;top:2730px" width="1200" height="60" viewBox="0 2730 1200 60">
    <line x1="50" y1="2756" x2="64" y2="2756" stroke="#cfcfcf" stroke-width="1.5"/>
    <polyline points="54,2752 50,2756 54,2760" fill="none" stroke="#cfcfcf" stroke-width="1.5"/>
    <line x1="1146" y1="2756" x2="1160" y2="2756" stroke="#cfcfcf" stroke-width="1.5"/>
    <polyline points="1156,2752 1160,2756 1156,2760" fill="none" stroke="#cfcfcf" stroke-width="1.5"/>
  </svg>

  <!-- contact -->
  <div class="mark-dot sm" style="left:444px;top:3084px"></div>
  <h2 class="abs serif" style="left:485px;top:3080px;font-size:30px">GET IN TOUCH</h2>
  <div class="abs field" style="left:202px;top:3145px;width:384px;height:46px;padding-top:15px">First Name</div>
  <div class="abs field" style="left:202px;top:3216px;width:384px;height:46px;padding-top:15px">Last Name</div>
  <div class="abs field" style="left:202px;top:3285px;width:384px;height:46px;padding-top:15px">Email Address</div>
  <div class="abs field" style="left:620px;top:3145px;width:383px;height:46px;padding-top:15px">Phone</div>
  <div class="abs field" style="left:620px;top:3216px;width:383px;height:115px;padding-top:15px">Message</div>
  <div class="abs btn btn-blue" style="left:495px;top:3363px;width:225px;height:41px">VIEW OUR ACCESSORIES</div>

  <!-- footer -->
  <div class="mark-dot" style="left:608px;top:3590px;width:44px;height:44px"></div>
  <div class="abs serif" style="left:0;width:1260px;top:3648px;text-align:center;font-size:23px;font-weight:400">FORNELLA</div>
  <nav class="foot-links">
    <a style="left:437px;top:3701px">Home</a>
    <a style="left:497px;top:3701px">About us</a>
    <a style="left:587px;top:3701px">Products</a>
    <a style="left:677px;top:3701px">Accessories</a>
    <a style="left:767px;top:3701px">Contact</a>
  </nav>
  <div class="foot-legal">
    <a style="left:450px;top:3756px">Privacy Policy</a>
    <a style="left:541px;top:3756px">Legal Notice</a>
  </div>
  <div class="abs social" style="left:662px;top:3748px"><span></span><span></span><span></span><span></span></div>
  <div class="abs" style="left:0;width:1260px;top:3845px;text-align:center;font-size:12px;color:#d8d8d8">© Copyright 2023 by <span style="color:#fff">fornella</span></div>

</div>
</body>
</html>
```